Surya Namaskar/Sun salutation theme based 12 months desk calendar for 2016 for an indian company

1. We are a corporate support services provider, providing services in Security Management, Fire Safety Management, facility management & HR Services based out of India. pls check website: www.brelvanta.co.in
2. Need a complete 12 months desk calendar design layout for 2016 including introductory page & end page,which can then be given for printing straightaway. The calendar should be so designed that when we open any month on the front side, the back side should also give out just the same month dates layout with space to note down any important work on a date etc..All important indian festivals, gazetted hoildays should be mentioned. Any information required can be provided by us
3. Since we give this calendars as part of new year gifts, our calendar has to compete for client desk space with other calendars, it must really be very sophisticated, sleek and attractive
4. Company logo, company contact details, website details and company works must be included in the calendar but in subtle, unobtrusive way. Few details like company logo etc, can be there on all pages.Am uploading some details, rest can be taken from the website, or can be provided
5. Calendar size should be aprx 17 cm * 17 cm including the space needed for spiral. Format should be CDR Ver13 or PDF
6. Theme: Surya Namaskar poses/Sun Salutation poses. These are twelve yoga poses, prescribed for mind /body rejuvenation. Poses 1-12 should be on months Jan16 to Dec 16. A very brief writeup on the same including the relevant mantras may also be included on the page
7. Any query , please mail to rohan.mehtra@brelvanta.co.in

Target Market(s)

corporate middle & senior management MNC clients

Industry/Entity Type

Security

Requirements
Must have
• 1.company logos/contact & website details/company works with related photographs.
• 2. surya namaskar poses with a very small brief/health benefit on poses/related mantras
• 3. Indian gazetted holidays & festivals earmarked
• 4. recommendation on the printing paper type & quality/colour of cardboard base & spiral binding
• 5. Attractive Top Introduction page & end page
Nice to have
• 1. photos of the company works
• 2. End page may be used for giving company details in details
• 3. Company logo on each page
• 4. The calendar goes to a variety of corporate clients including hotels, hospitals, shopping malls, manufacturing sector, clubs etc..just for info
• 5. Related photos/same model in all months
• 6. Beautiful Female models in poses
• 7. target audience : 95% male; majority age group: 35-55; middle & senior management
• However, very receptive to any new ideas. The designer has full liberty from our side. The final parameter is that the calendar should be so attractive that it can defeat any other desk calendar competition and win that one spot on the desk
• Any queries/details required, pls mail to rohan.mehtra@brelvanta.co.in
Should not have
• Religious overtones

```html
<!DOCTYPE html>
<html lang="en">
<head>
<meta charset="utf-8">
<title>Brelvanta Desk Calendar – March</title>
<link href="https://fonts.googleapis.com/css2?family=Montserrat:wght@700&family=Open+Sans:wght@700&family=Josefin+Sans:wght@700&display=swap" rel="stylesheet">
<style>
  :root {
    --cream: #f8e9cb;
    --green: #2e6e63;
    --orange: #f3ae1f;
    --white: #ffffff;
  }
  html, body {
    margin: 0;
    padding: 0;
    width: 1200px;
    height: 1200px;
    overflow: hidden;
    background: var(--cream);
  }
  .page {
    position: relative;
    width: 1156px;
    height: 1156px;
    background: var(--cream);
    transform: scale(1.03806);
    transform-origin: 0 0;
    overflow: hidden;
  }
  .decor {
    position: absolute;
    inset: 0;
    width: 1156px;
    height: 1156px;
  }
  .month-title {
    position: absolute;
    left: 235px;
    width: 400px;
    top: 414px;
    margin: 0;
    text-align: center;
    font-family: "Montserrat", sans-serif;
    font-weight: 700;
    font-size: 62px;
    letter-spacing: 1px;
    color: var(--green);
  }
  .weekdays {
    position: absolute;
    left: 48px;
    top: 492px;
    width: 777px;
    display: grid;
    grid-template-columns: repeat(7, 1fr);
    font-family: "Open Sans", sans-serif;
    font-weight: 700;
    font-size: 21px;
    color: var(--green);
    text-align: center;
  }
  .month-grid {
    position: absolute;
    left: 47px;
    top: 531px;
    width: 777px;
    height: 556px;
    display: grid;
    grid-template-columns: repeat(7, 1fr);
    grid-template-rows: repeat(5, 1fr);
    border-top: 2px solid var(--green);
    border-left: 2px solid var(--green);
    box-sizing: border-box;
  }
  .day {
    border-right: 2px solid var(--green);
    border-bottom: 2px solid var(--green);
    text-align: right;
    padding: 2px 6px 0 0;
    font-family: "Josefin Sans", sans-serif;
    font-weight: 700;
    font-size: 32px;
    line-height: 1.2;
    color: var(--green);
  }
  .day.holiday { color: var(--orange); }
  .brand {
    position: absolute;
    left: 1000px;
    top: 1040px;
    width: 150px;
    text-align: center;
    color: var(--white);
    font-family: "Open Sans", sans-serif;
    font-weight: 700;
  }
  .brand-dot {
    display: block;
    width: 26px;
    height: 26px;
    margin: 0 auto 8px;
    border-radius: 50%;
    background: var(--white);
  }
  .brand-name {
    display: block;
    font-size: 16px;
    letter-spacing: 0.5px;
  }
  .brand-line {
    display: block;
    font-size: 6px;
    line-height: 1.4;
  }
</style>
</head>
<body>
  <main class="page">
    <svg class="decor" viewBox="0 0 1156 1156" aria-hidden="true">
      <path class="accent-swoosh" fill="var(--orange)"
            d="M900 296 C1000 272 1100 160 1156 45 L1156 150 C1100 230 1000 292 900 296 Z"/>
      <path class="header-band" fill="var(--green)" stroke="var(--cream)" stroke-width="3"
            d="M-5 315 C200 300 380 290 500 293 C650 297 780 312 880 301 C1000 290 1100 222 1160 150 L1160 382 C1050 378 950 372 850 360 C700 342 560 328 420 330 C250 333 100 350 -5 368 Z"/>
      <circle class="corner-disc" cx="1165" cy="1165" r="205" fill="var(--green)"/>
    </svg>

    <h1 class="month-title">MARCH</h1>

    <div class="weekdays">
      <span>SUN</span><span>MON</span><span>TUE</span><span>WED</span><span>THU</span><span>FRI</span><span>SAT</span>
    </div>

    <div class="month-grid">
      <div class="day"></div><div class="day"></div>
      <div class="day">1</div><div class="day">2</div><div class="day">3</div><div class="day">4</div><div class="day">5</div>
      <div class="day">6</div><div class="day">7</div><div class="day">8</div><div class="day">9</div><div class="day">10</div><div class="day">11</div><div class="day">12</div>
      <div class="day">13</div><div class="day">14</div><div class="day">15</div><div class="day">16</div><div class="day">17</div><div class="day">18</div><div class="day">19</div>
      <div class="day">20</div><div class="day">21</div><div class="day">22</div><div class="day">23</div><div class="day holiday">24</div><div class="day holiday">25</div><div class="day">26</div>
      <div class="day">27</div><div class="day">28</div><div class="day">29</div><div class="day">30</div><div class="day">31</div><div class="day"></div><div class="day"></div>
    </div>

    <div class="brand">
      <span class="brand-dot"></span>
      <span class="brand-name">BRELVANTA</span>
      <span class="brand-line">Support services, done with care</span>
      <span class="brand-line">Quality assured since 2001</span>
    </div>
  </main>
</body>
</html>
```